Pine Ledge Traders, LLC- Global Beverage Company with 100% Cold Chain Logistics

Hey All, My Name is Dale, I am a young business owner in a competitive export space, but my niche is that I am shipping all of my beer around the world, "100% Cold Chain". This model is more costly, but it protects the integrity of the beer itself and will give folks in foreign countries the best representation of what US Craft Beer has to offer.

I am not a branding guy and don't claim to be one, I am a salesperson first, and will be referring to all of you to create something great that will be memorable.

I am looking for a basic Business Card Design for my Craft Beer Export company. I sell US Craft Beer in several countries around the globe. Austrailia, China, Taiwan, Chile, France, New Zealand... to name a few.

I am looking for a sleek, modern, and fresh design. Quickly!

Thanks for your consideration!

Cheers,

Dale

Target Market(s)

International

Contact Information for Business Card

Dale Corrigan
Founder- Roaming Hops Guy
Dale@PineLedgeTraders.example
@RoamingHopsGuy- Instagram only
www.Pineledgetraders.example
@PineLedgeTradersAU- Instagram Only

Font styles to use
Serif

Colors
0592cd
ffffff

Requirements
Must have
• Name-
• Title-
• Email-
• Social Media Handle-
• Company Website-
Nice to have
• Nice Logo/ Images on Card
Should not have
• Tacky Beer Images

```html
<!DOCTYPE html>
<html lang="en">
<head>
<meta charset="utf-8">
<title>Pine Ledge Traders – Business Card</title>
<link rel="stylesheet" href="https://fonts.googleapis.com/css2?family=Lato:wght@400;700;900&display=swap">
<style>
  :root {
    --brand-blue: #0592cd;
    --paper: #ffffff;
    --ink: #3a3a3a;
    --rule: #bdbdbd;
    --backdrop: #e9e9ea;
    --map-pale: #eef6fb;
    --map-mid: #cde6f5;
  }
  * { box-sizing: border-box; margin: 0; padding: 0; }
  html, body {
    width: 1200px; height: 844px; overflow: hidden;
    background: var(--backdrop);
    font-family: "Lato", Arial, sans-serif;
  }
  .canvas {
    position: relative; width: 1200px; height: 844px;
    display: flex; align-items: center; justify-content: center; gap: 48px;
  }
  .card {
    position: relative; width: 530px; height: 303px;
    background: var(--paper);
    box-shadow: 0 6px 18px rgba(0,0,0,.18);
    overflow: hidden;
  }

  /* Front */
  .brand {
    position: absolute; top: 46px; right: 48px;
    display: flex; flex-direction: column; align-items: flex-start;
  }
  .brand-row { display: flex; align-items: center; gap: 12px; }
  .brand-square {
    width: 42px; height: 42px; border-radius: 6px; background: var(--brand-blue);
  }
  .brand-name {
    color: var(--brand-blue); font-weight: 900; font-size: 22px;
    line-height: 20px; letter-spacing: .5px; text-transform: uppercase;
  }
  .brand-tagline {
    margin-top: 10px; color: var(--ink); font-weight: 900;
    font-size: 14px; letter-spacing: .6px; text-transform: uppercase;
  }
  .top-rule {
    position: absolute; top: 150px; right: 48px; width: 260px;
    height: 1px; background: var(--rule);
  }
  .person { position: absolute; left: 34px; top: 180px; }
  .person-name {
    color: var(--brand-blue); font-weight: 700; font-size: 19px;
    letter-spacing: .5px; text-transform: uppercase;
  }
  .person-title { color: var(--ink); font-size: 14px; margin-top: 2px; }
  .handle {
    display: flex; align-items: center; gap: 7px; margin-top: 8px;
    color: var(--ink); font-size: 14px;
  }
  .handle-dot { width: 16px; height: 16px; border-radius: 50%; background: var(--brand-blue); }
  .mid-rule {
    position: absolute; left: 230px; top: 222px; width: 260px;
    height: 1px; background: var(--rule);
  }
  .contact {
    position: absolute; left: 34px; bottom: 22px; right: 30px;
    display: flex; justify-content: space-between;
    font-size: 13px; color: var(--ink);
  }
  .contact-label { color: var(--brand-blue); font-weight: 700; margin-right: 5px; }

  /* Back */
  .map-area {
    position: absolute; inset: 0 0 46px 0;
    background: linear-gradient(160deg, var(--map-pale) 0%, var(--map-mid) 55%, var(--map-pale) 100%);
  }
  .country-band {
    position: absolute; left: 0; right: 0; bottom: 0; height: 70px;
    background: linear-gradient(to bottom, rgba(5,146,205,0) 0%, var(--brand-blue) 55%);
    display: flex; align-items: flex-end; justify-content: center;
    padding-bottom: 14px;
  }
  .countries { color: var(--paper); font-size: 15px; letter-spacing: .3px; }
</style>
</head>
<body>
<main class="canvas">
  <section class="card card-front">
    <div class="brand">
      <div class="brand-row">
        <span class="brand-square"></span>
        <span class="brand-name">Pine Ledge<br>Traders</span>
      </div>
      <p class="brand-tagline">100% Cold Chain Logistics</p>
    </div>
    <div class="top-rule"></div>

    <div class="person">
      <h1 class="person-name">Dale Corrigan</h1>
      <p class="person-title">Founder - Roaming Hops Guy</p>
      <p class="handle"><span class="handle-dot"></span>@RoamingHopsGuy</p>
    </div>
    <div class="mid-rule"></div>

    <div class="contact">
      <p><span class="contact-label">E:</span>Dale@PineLedgeTraders.example</p>
      <p><span class="contact-label">W:</span>www.Pineledgetraders.example</p>
    </div>
  </section>

  <section class="card card-back">
    <div class="map-area" role="img" aria-label="Dotted world map in brand blue showing the export markets"></div>
    <div class="country-band">
      <p class="countries">Australia | China | Taiwan | Chile | France | New Zealand</p>
    </div>
  </section>
</main>
</body>
</html>
```